Business card for Crestline Bathrooms

Please design a business card for our bathroom renovation business. You can use my existing logo, but if you have an idea to modernize it, I would like to see it. Please see attached files first. I would like to use the blue and the orange theme. I like the concept of using the shower head in the logo. Please find following a design (or two) that I have been trying to create with my limited resources. That design was for a sign, but I was going to adopt it and use it as a business card as well. I like the concept of the water splash but I don’t think it “flows” nicely together with the logo. Another thought is that maybe creating the logo out of water splash could work and have a dramatic effect (like the water text and the butterfly picture attached with similar background instead of white). If the above doesn’t work I would like to see a modern simplified design. One of the attached files named as the unwanted business card has all the details that I want included in the business card. Please note that it is two sided.
Updates

I am very thankful for the designs that I have received, but they are very similar and only a couple of attempts to do something with the water splash as per my original brief. Modernizing the logo and having it made out of out of water splash with the orange as color accent could work and have a dramatic effect (like the water text and the butterfly picture attached with similar background instead of white). Please do not use the butterfly itself! This is just an example that images can be created out of water splash.

Contact Information for Business Card

all the details are on the unwonted business card file included

Colors
3176b5

Requirements
Nice to have
• Copied from the brief:
• ... maybe creating the logo out of water splash could work and have a dramatic effect (like the water text and the butterfly picture attached with similar background instead of white). Please do not use the butterfly itself!
Should not have
• I am getting designs with a butterfly. The butterfly picture was an example of creating something from a water splash. The butterfly itself has no association with anything other than the concept of creating a logo out of water splash. Sorry, I thought I was clear in the brief.

```html
<!DOCTYPE html>
<html lang="en">
<head>
<meta charset="utf-8">
<title>Crestline Bathrooms – Business Card</title>
<link rel="stylesheet" href="https://fonts.googleapis.com/css2?family=Roboto:wght@400;500&family=Roboto+Condensed:wght@700&display=swap">
<style>
  :root {
    --backdrop: #2a2a2b;
    --card-white: #f4f4f3;
    --navy: #053f6a;
    --coral: #ec7c6c;
    --text-grey: #555a5e;
    --white: #ffffff;
  }
  * { box-sizing: border-box; margin: 0; padding: 0; }
  html, body { width: 1200px; height: 960px; overflow: hidden; }
  body {
    background: var(--backdrop);
    position: relative;
    font-family: "Roboto", Arial, sans-serif;
  }
  .card {
    position: absolute;
    left: 320px;
    width: 600px;
    height: 345px;
    border-radius: 18px;
    overflow: hidden;
  }
  .card-front { top: 100px; background: var(--card-white); }
  .card-back { top: 492px; background: var(--navy); color: var(--white); text-align: center; }

  .shower-art {
    position: absolute;
    left: 240px;
    top: 18px;
    width: 360px;
    height: 327px;
    background: radial-gradient(ellipse at 38% 30%, rgba(236,124,108,0.45), rgba(236,124,108,0) 45%),
                radial-gradient(ellipse at 78% 55%, rgba(5,63,106,0.35), rgba(5,63,106,0) 60%);
  }
  .person-name {
    position: absolute;
    left: 31px;
    top: 171px;
    font-family: "Roboto Condensed", "Arial Narrow", sans-serif;
    font-weight: 700;
    font-size: 20px;
    color: var(--navy);
    letter-spacing: 0.2px;
  }
  .address {
    position: absolute;
    left: 31px;
    top: 211px;
    font-size: 14px;
    line-height: 18px;
    color: var(--text-grey);
  }
  .contact-list {
    position: absolute;
    left: 31px;
    top: 256px;
    list-style: none;
    font-size: 14px;
    color: var(--text-grey);
  }
  .contact-list li { display: flex; align-items: center; height: 19px; }
  .contact-list svg { width: 13px; height: 13px; margin-right: 9px; fill: var(--navy); flex: none; }

  .brand-name {
    position: absolute;
    left: 0; right: 0;
    top: 78px;
    font-size: 34px;
    font-weight: 500;
    color: var(--white);
    letter-spacing: 0.5px;
  }
  .brand-mark {
    display: inline-block;
    width: 14px; height: 14px;
    border-radius: 50%;
    background: var(--white);
    margin-right: 10px;
    vertical-align: middle;
  }
  .services {
    position: absolute;
    left: 0; right: 0;
    top: 189px;
    list-style: none;
    font-size: 14px;
    line-height: 18px;
  }
  .memberships {
    position: absolute;
    left: 0; right: 0;
    top: 275px;
    display: flex;
    justify-content: center;
    align-items: center;
    gap: 14px;
  }
  .badge-square { width: 32px; height: 34px; border-radius: 6px; background: var(--white); }
  .badge-divider { width: 1px; height: 34px; background: var(--white); opacity: 0.8; }
  .badge-wide { width: 116px; height: 26px; border-radius: 3px; background: var(--white); }
</style>
</head>
<body>
  <section class="card card-front" aria-label="Business card front">
    <div class="shower-art" role="img" aria-label="Illustration of a shower head with spraying water and a curving hose"></div>
    <h1 class="person-name">DANIEL MARLOWE</h1>
    <p class="address">PO Box 41<br>Crestwood 2620</p>
    <ul class="contact-list">
      <li><svg viewBox="0 0 16 16"><path d="M3.6 1.2l2.3 2.8c.3.4.3 1-.1 1.4L4.6 6.6c.9 2 2.7 3.8 4.8 4.8l1.2-1.2c.4-.4 1-.4 1.4-.1l2.8 2.3c.4.4.4 1-.1 1.4l-1.4 1.2C9 15.7.3 7 1 2.7L2.2 1.3c.4-.5 1-.5 1.4-.1z"/></svg>0400 123 456</li>
      <li><svg viewBox="0 0 16 16"><path d="M4.5 0h7A1.5 1.5 0 0 1 13 1.5v13a1.5 1.5 0 0 1-1.5 1.5h-7A1.5 1.5 0 0 1 3 14.5v-13A1.5 1.5 0 0 1 4.5 0zM5 2v10h6V2H5zm3 11a1 1 0 1 0 0 2 1 1 0 0 0 0-2z"/></svg>6200 1234</li>
      <li><svg viewBox="0 0 16 16"><path d="M1 3h14v1.2L8 8.6 1 4.2V3zm0 2.9l7 4.4 7-4.4V13H1V5.9z"/></svg>daniel@crestlinebathrooms.com.au</li>
      <li><svg viewBox="0 0 16 16"><circle cx="8" cy="8" r="7"/><path d="M1 8h14M8 1c2.5 2.5 2.5 11.5 0 14M8 1c-2.5 2.5-2.5 11.5 0 14" stroke="#f4f4f3" stroke-width="1" fill="none"/></svg>crestlinebathrooms.com.au</li>
    </ul>
  </section>

  <section class="card card-back" aria-label="Business card back">
    <div class="brand-name"><span class="brand-mark"></span>Crestline Bathrooms</div>
    <ul class="services">
      <li>Complete Bathroom Renovations &amp; Remodelling</li>
      <li>Highly Skilled &amp; Qualified Tradespeople</li>
      <li>Professional Service From Concept To Completion</li>
      <li>All Work Guaranteed</li>
    </ul>
    <div class="memberships">
      <span class="badge-square" role="img" aria-label="Industry association membership badge"></span>
      <span class="badge-divider"></span>
      <span class="badge-wide" role="img" aria-label="Builders association membership badge"></span>
    </div>
  </section>
</body>
</html>
```